13 Varno - new website design project

Our company Varno Electrical is developing a new lead generation website focused on Electrical, LED Lighting and Solar Power. We need a high converting website.

Example of our current website is www.varnoelectrical-example.com.au You can take content from this website for this new design. Our colours are red, black and white. For our new website we would like to promote Varno, Spark Every Day. Please listen to the jingle.

The below link is the company jingle that we have developed.
http://www.tunecraftdemo.com.au/vrn-tc-v1/

The key for this brief is to generate leads for Electrical, LED Lighting (for commercial) and Solar Power & Storage.

Target Market(s)

Business owners in Melbourne Victoria

Number of Pages Required

4 page

Colors
ec1f27
ffffff

Requirements
Must have
• This page must be clean, be in line with company branding and a high converting lead website.

```html
<!DOCTYPE html>
<html lang="en">
<head>
<meta charset="utf-8">
<title>Varno Electrical</title>
<link href="https://fonts.googleapis.com/css2?family=Lato:wght@300;400;700;900&display=swap" rel="stylesheet">
<style>
:root{
  --red:#ec1f27;
  --ink:#1d1d1f;
  --nav:#2c2d31;
  --grey-bg:#f1f1f1;
  --text:#555;
  --muted:#777;
  --white:#fff;
  --footer:#efefef;
  --bar:#333437;
}
*{box-sizing:border-box;margin:0;padding:0}
html,body{width:1200px;height:3291px;overflow:hidden;background:var(--white)}
body{position:relative;font-family:'Lato',sans-serif;color:var(--text)}
.abs{position:absolute}

/* header */
.social{left:86px;top:68px;display:flex;gap:20px}
.social span{width:22px;height:22px;background:var(--ink);border-radius:3px;display:block}
.brand{left:460px;top:28px;width:280px;text-align:center}
.brand-name{display:flex;align-items:center;justify-content:center;gap:10px;font-weight:900;font-size:54px;color:var(--ink);line-height:1;letter-spacing:1px;white-space:nowrap}
.brand-name i{width:18px;height:18px;background:var(--red);display:block;flex:none}
.brand-tag{font-size:17px;font-weight:700;color:var(--ink);margin-top:6px}
.phone{right:86px;top:62px;font-size:27px;color:var(--ink);display:flex;align-items:center;gap:8px}
.phone b{color:var(--red);font-weight:400}

.nav{left:86px;top:149px;width:1028px;height:64px;background:var(--nav);display:flex;justify-content:space-around;align-items:center;padding:0 20px}
.nav a{color:var(--white);font-size:16px;text-decoration:none;letter-spacing:.3px}

/* hero */
.hero{left:0;top:213px;width:1200px;height:474px;background:var(--red)}
.hero-art{left:99px;top:241px;width:340px;height:395px;border-radius:40% 40% 30% 30%;background:radial-gradient(circle at 50% 35%,#f6c24a 0,#b89a6b 45%,#8a6a4f 75%,rgba(138,106,79,0) 76%)}
.hero-copy{right:86px;top:322px;text-align:right;color:var(--white)}
.hero-kicker{font-size:28px;font-weight:300;letter-spacing:1px}
.hero-title{font-size:31px;font-weight:900;margin-top:10px}
.hero-sub{font-size:17px;margin-top:14px}
.btn-light{right:86px;top:476px;width:146px;height:42px;background:var(--white);color:var(--red);font-size:16px;display:flex;align-items:center;justify-content:center;border-radius:2px}
.dots{right:86px;top:549px;display:flex;gap:4px}
.dots span{width:15px;height:15px;border:2px solid var(--white);border-radius:50%}
.dots span.on{background:var(--white)}

/* service cards */
.card{top:652px;width:324px;height:318px}
.card-label{position:absolute;left:92px;bottom:24px;width:232px;height:60px;background:var(--nav);color:var(--white);font-size:27px;display:flex;align-items:center;justify-content:center;letter-spacing:.5px}
.card-label.hot{background:var(--red)}
.card.elec{left:86px;background:linear-gradient(135deg,#1d3f6b,#3a6aa0 45%,#c84a3a 75%,#2a2a34)}
.card.led{left:439px;background:radial-gradient(circle at 55% 35%,#ffe6a6,#e7a24a 40%,#8a4a1c 85%)}
.card.led .card-label{left:46px}
.card.solar{left:790px;background:linear-gradient(180deg,#e8dcc4,#d8c09a 55%,#8f8a84)}

/* section headings */
.section-title{left:0;width:1200px;text-align:center;color:var(--red);font-size:28px;font-weight:400}
.section-sub{left:300px;width:600px;text-align:center;font-size:13px;line-height:25px;color:var(--muted)}

.about-bg{left:0;top:1025px;width:1200px;height:495px;background:var(--grey-bg)}
.video{left:103px;top:1198px;width:404px;height:246px;background:linear-gradient(160deg,#3b3b3f,#6d6a66 50%,#2b3a58)}
.play{left:279px;top:1303px;width:52px;height:36px;background:#111;border-radius:8px}
.play svg{position:absolute;left:18px;top:10px}
.video-bar{left:103px;top:1428px;width:404px;height:16px;background:#151515}
.about-text{left:531px;top:1204px;width:568px;font-size:13px;line-height:24px;color:var(--text)}
.about-text p+p{margin-top:18px}
.btn-red{left:531px;top:1422px;width:88px;height:31px;background:var(--red);color:var(--white);font-size:12px;display:flex;align-items:center;justify-content:center;border-radius:2px}

/* why */
.worker{left:88px;top:1678px;width:373px;height:523px;background:linear-gradient(180deg,#f4f4f4 0,#d9dde3 30%,#2c3f5c 60%,#3e5c86 100%);border-radius:6px 6px 0 0}
.why-item{left:500px;width:620px;display:flex;gap:38px}
.why-icon{width:53px;height:53px;border-radius:50%;flex:none;display:flex;align-items:center;justify-content:center}
.why-item h3{color:var(--red);font-size:18px;font-weight:700;letter-spacing:.3px;margin-top:-4px}
.why-item p{font-size:13px;line-height:21px;color:var(--text);margin-top:6px}

/* testimonials */
.testi{left:0;top:2201px;width:1200px;height:373px;background:linear-gradient(135deg,#ea4a47,#f27068 50%,#e8403e)}
.testi-title{left:0;top:2265px;width:1200px;text-align:center;color:var(--white);font-size:28px}
.quote-mark{left:580px;top:2325px;color:var(--white);font-size:52px;font-weight:900;line-height:1}
.quote-box{left:268px;top:2354px;width:664px;height:101px;border:1px solid rgba(255,255,255,.55);color:var(--white);font-size:13px;line-height:22px;padding:20px}
.quote-name{left:0;top:2482px;width:1200px;text-align:center;color:var(--white);font-size:16px}
.quote-name small{font-size:13px;border-left:1px solid var(--white);padding-left:8px;margin-left:6px}
.arrow{top:2372px}

/* clients */
.client{top:2769px;width:200px;height:92px;border:1px solid #e6e6e6;display:flex;align-items:center;justify-content:center;gap:8px;font-size:20px;font-weight:700;white-space:nowrap}
.client.active{border-color:var(--red)}
.client i{width:14px;height:14px;display:block;flex:none}

/* footer */
.footer{left:0;top:3006px;width:1200px;height:226px;background:var(--footer)}
.footer-brand{left:88px;top:3040px;width:280px}
.footer-brand .brand-name{font-size:66px;justify-content:flex-start}
.footer-brand .brand-tag{font-size:20px}
.f-head{font-size:17px;color:var(--ink);letter-spacing:.5px}
.f-list{font-size:12px;line-height:21px;color:var(--ink)}
.f-row{display:flex;align-items:center;gap:8px}
.f-social{display:flex;gap:14px;margin-top:10px}
.f-social span{width:14px;height:14px;background:var(--ink);display:block;border-radius:2px}
.f-social .like{width:100px;background:#4a6aa8}
.bottom-bar{left:0;top:3232px;width:1200px;height:59px;background:var(--bar);color:var(--white);font-size:12px;display:flex;align-items:center;justify-content:center}
</style>
</head>
<body>

<header>
  <div class="abs social"><span></span><span></span><span></span></div>
  <div class="abs brand">
    <div class="brand-name"><i></i>VARNO</div>
    <div class="brand-tag">Spark Every Day</div>
  </div>
  <div class="abs phone">
    <svg width="22" height="22" viewBox="0 0 24 24"><path fill="#ec1f27" d="M6.6 10.8a15 15 0 0 0 6.6 6.6l2.2-2.2a1 1 0 0 1 1-.25 11.4 11.4 0 0 0 3.6.57 1 1 0 0 1 1 1V20a1 1 0 0 1-1 1A17 17 0 0 1 3 4a1 1 0 0 1 1-1h3.5a1 1 0 0 1 1 1c0 1.25.2 2.45.57 3.6a1 1 0 0 1-.25 1z"/></svg>
    <span><b>-</b> 139 420</span>
  </div>
  <nav class="abs nav">
    <a>HOME</a><a>VARNO STORY</a><a>OUR WORK</a><a>ELECTRICAL</a><a>LED LIGHTING</a><a>SOLAR POWER</a><a>CONTACT US</a>
  </nav>
</header>

<section>
  <div class="abs hero"></div>
  <div class="abs hero-art" role="img" aria-label="Illustration of a floating island with a solar panel, a sun and clouds"></div>
  <div class="abs hero-copy">
    <div class="hero-kicker">VARNO ELECTRICAL IS DEVELOPING</div>
    <div class="hero-title">A NEW LEAD GENERATION SOLAR POWER</div>
    <div class="hero-sub">Australia's largest fully integrated Electrical &amp; Energy Solutions provider</div>
  </div>
  <div class="abs btn-light">Read More</div>
  <div class="abs dots"><span></span><span class="on"></span><span></span></div>

  <div class="abs card elec" role="img" aria-label="Photo of coloured electrical cables"><div class="card-label">ELECTRICAL</div></div>
  <div class="abs card led" role="img" aria-label="Photo of a glowing LED bulb"><div class="card-label hot">LED LIGHTING</div></div>
  <div class="abs card solar" role="img" aria-label="Photo of solar panels and wind turbines at sunset"><div class="card-label">SOLAR POWER</div></div>
</section>

<section>
  <div class="abs about-bg"></div>
  <h2 class="abs section-title" style="top:1086px">About Varno Electrical</h2>
  <p class="abs section-sub" style="top:1133px">Varno Electrical was formed to be an expert Electricity Contracting Company providing services to all Residential and Commercial Customers.</p>
  <div class="abs video" role="img" aria-label="Video still of two presenters beside a solar panel"></div>
  <div class="abs play"><svg width="16" height="16" viewBox="0 0 16 16"><path fill="#fff" d="M2 0l14 8-14 8z"/></svg></div>
  <div class="abs video-bar"></div>
  <div class="abs about-text">
    <p>Electrical and Energy Solutions are at the forefront of our company. Varno Electrical has a long history in Electrical, LED Lighting and Solar Power and just like the Cougar, we will strive to be fierce &amp; agile in an effort to exceed our customer's expectations and develop stronger links with all our business partners &amp; community.</p>
    <p>Varno Electrical is an expert Electrical Company providing services to all Residential and Commercial customers. With over 10 years of experience, Varno Electrical has developed a highly-experienced team of professionals that ensure all our customer expectations are exceeded.</p>
  </div>
  <div class="abs btn-red">Read More</div>
</section>

<section>
  <h2 class="abs section-title" style="top:1573px">Why Choose Us?</h2>
  <p class="abs section-sub" style="top:1620px">Varno Electrical was formed to be an expert Electricity Contracting Company providing services to all Residential and Commercial Customers.</p>
  <div class="abs worker" role="img" aria-label="Photo of an electrician in a hard hat with a tool belt"></div>

  <div class="abs why-item" style="top:1700px">
    <div class="why-icon" style="background:#f4a99a"><svg width="26" height="26" viewBox="0 0 24 24"><path fill="#fff" d="M21 6.5l-3.5 3.5-3-3L18 3.5A6 6 0 0 0 10 11L3 18l3 3 7-7a6 6 0 0 0 8-7.5z"/></svg></div>
    <div><h3>PROFESSIONAL SERVICE</h3><p>When you hire a Varno Electrical Electrician you will get a professional and<br>well-presented Electrician that comes skilled and ready to do the job.</p></div>
  </div>
  <div class="abs why-item" style="top:1794px">
    <div class="why-icon" style="background:#f28b84"><svg width="26" height="26" viewBox="0 0 24 24"><path fill="none" stroke="#fff" stroke-width="3" d="M5 12l5 5 9-10"/></svg></div>
    <div><h3>5 YEAR WORKMANSHIP GUARANTEE</h3><p>You can buy with confidence as all of our work has a 5 year workmanship guarantee.<br>For your peace of mind, we unconditionally back our electrical work. We will come back<br>to fix any problems at our own expense.</p></div>
  </div>
  <div class="abs why-item" style="top:1901px">
    <div class="why-icon" style="background:#f3b9b0"><svg width="26" height="26" viewBox="0 0 24 24"><rect x="3" y="6" width="18" height="12" rx="2" fill="#5bbfb5"/><circle cx="12" cy="12" r="3" fill="#fff"/></svg></div>
    <div><h3>VALUE FOR MONEY</h3><p>We provide extremely competitive pricing, which means you get value for money on<br>quality that is comparable to the best in the industry.</p></div>
  </div>
  <div class="abs why-item" style="top:1991px">
    <div class="why-icon" style="background:#cfe0a8"><svg width="26" height="26" viewBox="0 0 24 24"><path fill="none" stroke="#fff" stroke-width="2.5" d="M12 4l4 6H8zM5 18l3-6M19 18l-3-6M6 19h12"/></svg></div>
    <div><h3>ENVIRONMENTALLY FRIENDLY</h3><p>We a committed to reducing carbon emissions by installing Solar Power and upgrading<br>sites to LED Lighting. In addition to reducing the carbon emissions we recycle<br>Fluorescent Tubes, Highbay Globes, Metal and Cardboard.</p></div>
  </div>
  <div class="abs why-item" style="top:2103px">
    <div class="why-icon" style="background:#f1c7bf"><svg width="26" height="26" viewBox="0 0 24 24"><path fill="#ec5a55" d="M2 12a10 10 0 0 1 20 0z"/><path fill="none" stroke="#5bbfb5" stroke-width="2" d="M12 12v7a2 2 0 0 1-4 0"/></svg></div>
    <div><h3>FULLY INSURED</h3><p>Varno Electrical is fully insured and equipped to handle break downs and service call outs.</p></div>
  </div>
</section>

<section>
  <div class="abs testi"></div>
  <h2 class="abs testi-title">Our Testimonials</h2>
  <div class="abs quote-mark">&ldquo;</div>
  <div class="abs quote-box">The service, communication and after sales service of Varno Electrical has been awesome. We would strongly recommend them to any business contemplating upgrading their lighting or any other electrical work</div>
  <div class="abs quote-name">CORIN ASHDALE <small>Executive Dunmarrow Surplus</small></div>
  <svg class="abs arrow" style="left:84px" width="20" height="32" viewBox="0 0 20 32"><path d="M17 2L3 16l14 14" fill="none" stroke="#fff" stroke-width="2.5"/></svg>
  <svg class="abs arrow" style="left:1098px" width="20" height="32" viewBox="0 0 20 32"><path d="M3 2l14 14L3 30" fill="none" stroke="#fff" stroke-width="2.5"/></svg>
</section>

<section>
  <h2 class="abs section-title" style="top:2638px">Our Clients</h2>
  <p class="abs section-sub" style="top:2685px">Varno Electrical was formed to be an expert Electricity Contracting Company providing services to all Residential and Commercial Customers.</p>
  <div class="abs client" style="left:88px;color:#e25a6a">Plumvale</div>
  <div class="abs client" style="left:292px;color:#c33;font-size:18px"><i style="background:#f6e36a"></i>Dunmarrow Surplus</div>
  <div class="abs client" style="left:500px;color:#e87a7a;font-size:18px">Wrenfold Plumbing</div>
  <div class="abs client active" style="left:704px;color:#c8102e"><i style="background:#c8102e"></i>Grillora</div>
  <div class="abs client" style="left:913px;color:#8aa3bd">Fjelmark</div>
</section>

<footer>
  <div class="abs footer"></div>
  <div class="abs footer-brand">
    <div class="brand-name"><i></i>VARNO</div>
    <div class="brand-tag">Spark Every Day</div>
  </div>
  <div class="abs" style="left:522px;top:3030px">
    <div class="f-head">CONTACT US</div>
    <div class="f-list" style="margin-top:16px">
      <div class="f-row"><svg width="10" height="12" viewBox="0 0 10 14"><path fill="#1d1d1f" d="M5 0a5 5 0 0 1 5 5c0 4-5 9-5 9S0 9 0 5a5 5 0 0 1 5-5z"/></svg>- 22/48 Kestrel Rd, Glen Ridge, Vic 3150</div>
      <div class="f-row"><svg width="10" height="10" viewBox="0 0 24 24"><path fill="#1d1d1f" d="M6.6 10.8a15 15 0 0 0 6.6 6.6l2.2-2.2a1 1 0 0 1 1-.25 11.4 11.4 0 0 0 3.6.57 1 1 0 0 1 1 1V20a1 1 0 0 1-1 1A17 17 0 0 1 3 4a1 1 0 0 1 1-1h3.5a1 1 0 0 1 1 1c0 1.25.2 2.45.57 3.6a1 1 0 0 1-.25 1z"/></svg>- 139 420</div>
      <div class="f-row"><svg width="10" height="8" viewBox="0 0 12 9"><rect width="12" height="9" fill="#1d1d1f"/><path d="M0 0l6 5 6-5" fill="none" stroke="#fff"/></svg>- service@varnoelectrical-example.com.au</div>
    </div>
    <div class="f-social"><span></span><span></span><span></span><span class="like"></span></div>
  </div>
  <div class="abs" style="left:994px;top:3030px">
    <div class="f-head">SITE MAP</div>
    <div class="f-list" style="margin-top:16px">Led Lighting<br>Solar Power<br>Electrical<br>Career<br>Terms and Conditions<br>Privacy</div>
  </div>
  <div class="abs bottom-bar">Varno Electrical © 2017 All rights reserved.</div>
</footer>

</body>
</html>
```